Harborline Benches business cards

I’d like a business card design that includes my logo, a tag line and my contact info. Black, textured background. My contact info color should match the orange and blue gradients. Tagline under logo: “Wooden Tables and Furniture of the Highest Quality”

Target Market(s)

High end furniture buyers

Contact Information for Business Card

Contact info, logo and tagline

```html
<!DOCTYPE html>
<html lang="en">
<head>
<meta charset="utf-8">
<title>Harborline Benches – Business Cards</title>
<link rel="stylesheet" href="https://fonts.googleapis.com/css2?family=Tenor+Sans&family=Arimo:wght@400&family=Roboto+Condensed:wght@400&display=swap">
<style>
  :root {
    --page-bg: #9a9a9a;
    --card-bg: #232323;
    --card-edge: #d9531c;
    --orange: #ee6a2c;
    --orange-light: #f28a3c;
    --blue: #3a6fd8;
    --blue-light: #4aa6e6;
    --white: #f4f4f4;
  }
  * { box-sizing: border-box; margin: 0; padding: 0; }
  html, body {
    width: 1200px; height: 1050px; overflow: hidden;
    background: var(--page-bg);
  }
  .sheet {
    width: 1200px; height: 1050px;
    display: flex; flex-direction: column; align-items: center;
    justify-content: center; gap: 30px;
  }
  .card {
    position: relative;
    width: 840px; height: 480px;
    background-color: var(--card-bg);
    background-image:
      repeating-radial-gradient(circle at 30% 40%, rgba(255,255,255,0.015) 0 1px, transparent 1px 3px),
      repeating-linear-gradient(45deg, rgba(0,0,0,0.08) 0 1px, transparent 1px 4px);
    border-bottom: 5px solid var(--card-edge);
    border-radius: 3px;
    box-shadow: 0 14px 30px rgba(0,0,0,0.35);
    overflow: hidden;
  }

  /* Front */
  .tree-art {
    position: absolute; left: 50px; top: 40px;
    width: 400px; height: 435px;
    border-radius: 4px;
    background: linear-gradient(135deg, #e8602a 0%, #f28a3c 100%);
    opacity: 0.85;
  }
  .front-info {
    position: absolute; right: 60px; top: 95px;
    width: 360px; text-align: right;
    font-family: "Arimo", Arial, sans-serif;
    color: var(--white);
  }
  .brand-small {
    display: flex; align-items: center; justify-content: flex-end; gap: 10px;
    font-family: "Tenor Sans", sans-serif;
    font-size: 34px; color: var(--orange);
  }
  .brand-mark {
    width: 18px; height: 18px; border-radius: 50%;
    background: var(--orange);
    flex: none;
  }
  .tagline-small {
    font-family: "Roboto Condensed", sans-serif;
    font-size: 15px; margin-top: 6px;
    border-top: 1px solid var(--orange); padding-top: 4px;
  }
  .tag-blue { color: var(--blue); }
  .tag-orange { color: var(--orange); }
  .person-name {
    font-family: "Tenor Sans", sans-serif;
    font-size: 26px; color: var(--orange);
    margin-top: 22px; letter-spacing: 1px;
  }
  .person-title { font-size: 17px; margin-top: 2px; }
  .address { font-size: 17px; line-height: 1.35; margin-top: 18px; }
  .contact-list { list-style: none; margin-top: 16px; font-size: 17px; line-height: 1.5; }
  .contact-list li { display: flex; justify-content: flex-end; align-items: center; gap: 12px; }
  .contact-icon { width: 16px; height: 16px; fill: var(--orange); flex: none; }
  .contact-list .no-icon { padding-right: 28px; }

  /* Back */
  .back-logo {
    position: absolute; left: 0; right: 0; top: 150px;
    text-align: center;
  }
  .brand-large {
    display: inline-flex; align-items: center; gap: 16px;
    font-family: "Tenor Sans", sans-serif;
    font-size: 72px; color: var(--orange);
    padding-bottom: 8px;
    border-bottom: 1px solid var(--orange);
  }
  .brand-large .brand-mark { width: 30px; height: 30px; }
  .tagline-large {
    font-family: "Tenor Sans", sans-serif;
    font-size: 22px; letter-spacing: 1.5px; margin-top: 14px;
  }
</style>
</head>
<body>
<main class="sheet">

  <section class="card card-front">
    <div class="tree-art" role="img" aria-label="Illustration of a large bare branching tree in orange gradient"></div>
    <div class="front-info">
      <div class="brand-small"><span class="brand-mark"></span>Harborline Benches</div>
      <p class="tagline-small"><span class="tag-blue">Wooden Tables &amp; Furniture</span> <span class="tag-orange">of the Highest Quality</span></p>
      <p class="person-name">Daniel Whitcombe</p>
      <p class="person-title">Managing Director</p>
      <p class="address">412 Cedar Hollow Road<br>Bellport, Maine 04021</p>
      <ul class="contact-list">
        <li>555-214-7730
          <svg class="contact-icon" viewBox="0 0 16 16" aria-hidden="true"><path d="M3.5 1l2.5 3-1.5 1.6c.8 2 2.4 3.6 4.4 4.4L10.5 8.5l3 2.5-1.6 2.6c-5.3-.4-9.6-4.7-10-10z"/></svg></li>
        <li>555-309-4182
          <svg class="contact-icon" viewBox="0 0 16 16" aria-hidden="true"><path d="M4 1h8v14H4zM5.5 2.5v10h5v-10z"/></svg></li>
        <li>info@HarborlineBenches
          <svg class="contact-icon" viewBox="0 0 16 16" aria-hidden="true"><path d="M1 3h14v10H1zM2 4l6 5 6-5z"/></svg></li>
        <li class="no-icon">www.HarborlineBenches.com</li>
      </ul>
    </div>
  </section>

  <section class="card card-back">
    <div class="back-logo">
      <div class="brand-large"><span class="brand-mark"></span>Harborline Benches</div>
      <p class="tagline-large"><span class="tag-blue">Wooden Tables &amp; Furniture</span> <span class="tag-orange">of the Highest Quality</span></p>
    </div>
  </section>

</main>
</body>
</html>
```